SkyvornQ Business Cards and Stationary Design

Need a design for our business cards and stationary. I want to carry on the theme of the logo. I want the business cards to have a design on the back. I would like the business cards and the stationary to carry the same theme, design scheme, and branding

Target Market(s)

Airlines and Maintenance Facilities

Industry/Entity Type

Aviation

Contact Information for Business Card

Name
Position Title
Address: 4827 Trellis Hollow Road, Fort Pierce, Florida, 34951
Office Number
Mobile Number
Email
Website

Font styles to use
Serif
Sans Serif

Colors

Designer to choose colors to be used in the design.

```html
<!DOCTYPE html>
<html lang="en">
<head>
<meta charset="utf-8">
<title>SkyvornQ Business Card</title>
<link rel="stylesheet" href="https://fonts.googleapis.com/css2?family=Montserrat:wght@400;500;600;700;800&display=swap">
<style>
  :root {
    --backdrop: #e6e2dc;
    --card: #f4f2ef;
    --card-edge: #ffffff;
    --navy: #2b3340;
    --ink: #3b3e44;
    --sky: #2a9fd6;
    --brand-blue: #1f6fb4;
  }
  html, body {
    margin: 0;
    padding: 0;
    width: 1200px;
    height: 1047px;
    overflow: hidden;
    background: var(--backdrop);
    font-family: "Montserrat", sans-serif;
  }
  .card {
    position: absolute;
    left: 100px;
    top: 243px;
    width: 1000px;
    height: 560px;
    background: var(--card);
    border: 2px solid var(--card-edge);
    border-radius: 26px;
    box-shadow: 0 10px 40px rgba(60, 50, 40, 0.12);
    box-sizing: border-box;
  }
  .card__brand {
    position: absolute;
    left: 50px;
    top: 62px;
    margin: 0;
    font-size: 27px;
    font-weight: 800;
    letter-spacing: 5px;
    color: var(--navy);
  }
  .card__accent {
    position: absolute;
    left: 0;
    top: 120px;
    width: 9px;
    height: 86px;
    background: var(--sky);
    border-radius: 0 3px 3px 0;
  }
  .card__name {
    position: absolute;
    left: 50px;
    top: 127px;
    margin: 0;
    font-size: 40px;
    font-weight: 500;
    color: var(--sky);
  }
  .card__role {
    position: absolute;
    left: 50px;
    top: 178px;
    margin: 0;
    font-size: 23px;
    font-weight: 500;
    color: var(--ink);
  }
  .card__address {
    position: absolute;
    left: 50px;
    top: 258px;
    margin: 0;
    font-style: normal;
    font-size: 23px;
    line-height: 33px;
    color: var(--ink);
  }
  .card__contacts {
    position: absolute;
    left: 50px;
    top: 385px;
    margin: 0;
    padding: 0;
    list-style: none;
    font-size: 23px;
    line-height: 32px;
    color: var(--ink);
  }
  .card__contacts .label {
    color: var(--sky);
    font-weight: 500;
  }
  .card__mark {
    position: absolute;
    left: 470px;
    top: 170px;
    width: 470px;
    height: 260px;
    display: flex;
    align-items: center;
    justify-content: center;
    gap: 22px;
  }
  .card__mark-dot {
    width: 56px;
    height: 56px;
    border-radius: 50%;
    background: var(--brand-blue);
  }
  .card__mark-name {
    font-size: 66px;
    font-weight: 700;
    color: var(--brand-blue);
  }
</style>
</head>
<body>
  <section class="card" aria-label="SkyvornQ business card">
    <p class="card__brand">SKYVORNQ</p>
    <span class="card__accent"></span>
    <h1 class="card__name">Marcus Delane</h1>
    <p class="card__role">Co-Owner</p>
    <address class="card__address">
      4827 Trellis Hollow Road,<br>
      Fort Pierce,<br>
      Florida, 34951
    </address>
    <ul class="card__contacts">
      <li><span class="label">M:</span> (555) 318-4702</li>
      <li><span class="label">T:</span> 555-260-7719</li>
      <li><span class="label">E:</span> info@skyvornq.com</li>
      <li><span class="label">W:</span> www.skyvornq.com</li>
    </ul>
    <div class="card__mark">
      <span class="card__mark-dot"></span>
      <span class="card__mark-name">SkyvornQ</span>
    </div>
  </section>
</body>
</html>
```